Website to design and sell sundials: www.gnomonvale.com

We have a website that creates a free paper sundial, we want to migrate from this not profit free website to a website where we will continue offering the free paper sundial model but We will also offer a manufactured sundial and sell it.
In order to understand the project, please visit:
http://www.gnomonvale.com/vertical/sundial.html and
http://www.torvel.net/landing/

The website user journey should be redesigned, including the phases that are,
select language
Show product give info
Creation/edit sundial (could be one or more phases)
View created sundial
Buy sundial.

May some of them could be combined or splitted, what It have more sense.

Requirements
Must have
• A description page user journey offering freemium paper sundial and physical sundial to sell.
• A sundial creation page for "free" paper sundial
• A result page for paper sundial
• A sell page for physical

```html
<!DOCTYPE html>
<html lang="en">
<head>
<meta charset="utf-8">
<title>GnomonVale – Create your vertical sundial</title>
<link rel="stylesheet" href="https://fonts.googleapis.com/css2?family=Roboto:wght@400;500;700&family=Roboto+Condensed:wght@700&display=swap">
<style>
:root{
  --red:#c8161d;
  --red-dark:#a80f15;
  --amber:#f6a21b;
  --ink:#2b2b2b;
  --muted:#7a7a7a;
  --line:#d9d9d9;
  --white:#ffffff;
  --footer:#2e2e30;
  --footer-deep:#1f1f21;
  --hero-a:#3b3431;
  --hero-b:#7b6f66;
}
*{box-sizing:border-box;margin:0;padding:0}
html,body{width:795px;height:1200px;overflow:hidden}
body{font-family:"Roboto",Arial,sans-serif;color:var(--ink);background:var(--white);position:relative}
.site-header{position:absolute;top:0;left:0;width:795px;height:82px;background:var(--white)}
.brand{position:absolute;left:26px;top:24px;display:flex;align-items:center;gap:8px}
.brand-dot{width:20px;height:20px;border-radius:50%;background:var(--red)}
.brand-name{font-size:22px;font-weight:700;color:var(--red)}
.header-contact{position:absolute;left:470px;top:26px;display:flex;align-items:center;gap:8px}
.header-contact .icon{width:26px;height:26px;border-radius:50%;background:var(--red);display:flex;align-items:center;justify-content:center}
.header-contact p{font-size:11px;line-height:14px;color:var(--muted)}
.header-contact strong{color:var(--red);font-weight:500}
.lang-select{position:absolute;left:665px;top:33px;width:54px;height:16px;border:1px solid var(--line);font-size:9px;display:flex;align-items:center;gap:4px;padding-left:4px;color:var(--muted)}
.lang-select span.flag{width:12px;height:8px;background:linear-gradient(var(--red) 50%,#1b3c8c 50%)}
.main-nav{position:absolute;top:82px;left:0;width:795px;height:34px;background:var(--red);display:flex;justify-content:center}
.main-nav a{display:block;padding:0 22px;line-height:34px;font-size:10px;font-weight:500;color:var(--white);text-decoration:none;text-transform:uppercase}
.main-nav a.active{background:var(--amber)}
.hero{position:absolute;top:116px;left:0;width:795px;height:150px;background:linear-gradient(100deg,var(--hero-a),var(--hero-b) 60%,var(--hero-a))}
.hero h1{position:absolute;width:100%;top:58px;text-align:center;font-family:"Roboto Condensed",Arial,sans-serif;font-size:29px;color:var(--white);letter-spacing:.5px}
.location{position:absolute;top:266px;left:0;width:795px;height:352px;background:var(--white)}
.map{position:absolute;left:145px;top:48px;width:240px;height:290px;background:linear-gradient(160deg,#5f7a4c,#8a8c5e 45%,#4f6a7c);border:1px solid var(--line)}
.location-copy{position:absolute;left:403px;top:56px;width:330px}
.section-title{font-family:"Roboto Condensed",Arial,sans-serif;font-size:22px;color:var(--ink);margin-bottom:8px}
.location-copy p{font-size:9px;line-height:13px;color:var(--muted)}
.coords{display:flex;align-items:center;gap:6px;margin-top:44px;font-size:9px;color:var(--muted)}
.coords .field{width:50px;height:15px;border:1px solid var(--line)}
.btn-go{display:block;margin:12px 0 0 auto;width:34px;height:26px;background:var(--red);color:var(--white);border:0;font-size:12px;font-weight:700}
.location-copy h3{font-family:"Roboto Condensed",Arial,sans-serif;font-size:17px;margin:12px 0 6px}
.options{position:absolute;top:618px;left:0;width:795px;height:404px;background:var(--red)}
.options .section-title{position:absolute;top:30px;width:100%;text-align:center;color:var(--white);font-size:24px}
.photo{position:absolute;top:76px;width:286px;height:192px;border:3px solid var(--white);background:linear-gradient(140deg,#6b4a36,#a98c74 50%,#d9d2c4)}
.photo.wall{left:106px}
.photo.window{left:400px;background:linear-gradient(140deg,#3d4a3a,#7f8c83 50%,#d7dcd8)}
.choice{position:absolute;top:282px;display:flex;align-items:center;gap:6px;font-size:10px;color:var(--white)}
.radio{width:11px;height:11px;border-radius:50%;border:1.5px solid var(--white);background:transparent}
.radio.on{background:var(--white);box-shadow:inset 0 0 0 2px var(--red)}
.form-row{position:absolute;left:106px;display:flex;align-items:center;gap:8px;font-size:10px;color:var(--white)}
.form-row .field{height:17px;background:var(--white);font-size:8px;color:var(--ink);padding:3px 5px}
.form-row .opt{display:flex;align-items:center;gap:5px;margin-left:14px}
.btn-create{margin-left:16px;height:22px;padding:0 12px;background:var(--amber);color:var(--white);border:0;font-size:9px;font-weight:700;text-transform:uppercase}
.site-footer{position:absolute;top:1022px;left:0;width:795px;height:156px;background:var(--footer);color:#bdbdbd}
.footer-col{position:absolute;top:22px}
.footer-col h4{font-size:11px;font-weight:700;color:var(--white);text-transform:uppercase;margin-bottom:8px}
.footer-col p,.footer-col li{font-size:8.5px;line-height:13px;list-style:none}
.newsletter{left:62px;width:190px}
.newsletter .field{width:120px;height:17px;background:var(--white);margin-top:6px;font-size:8px;color:var(--muted);padding:3px 5px}
.newsletter .inline{display:flex;gap:4px}
.btn-subscribe{margin-top:6px;height:17px;padding:0 8px;background:var(--red);color:var(--white);border:0;font-size:8px;font-weight:700}
.contact{left:292px;width:180px}
.contact li{display:flex;align-items:center;gap:6px}
.contact .dot{width:6px;height:6px;border-radius:50%;background:var(--red)}
.social{display:flex;gap:6px;margin-top:6px}
.social span{width:14px;height:14px;background:var(--red)}
.links{left:522px;width:150px}
.footer-mark{position:absolute;left:690px;top:60px;width:40px;height:40px;border-radius:50%;background:var(--red)}
.copyright{position:absolute;top:1178px;left:0;width:795px;height:22px;background:var(--footer-deep);color:#9a9a9a;font-size:8px;text-align:center;line-height:22px}
</style>
</head>
<body>
<header class="site-header">
  <div class="brand"><span class="brand-dot"></span><span class="brand-name">GnomonVale.com</span></div>
  <div class="header-contact">
    <span class="icon"><svg width="12" height="12" viewBox="0 0 24 24"><path fill="#fff" d="M6.6 10.8a15 15 0 006.6 6.6l2.2-2.2a1 1 0 011-.25 11.4 11.4 0 003.6.57 1 1 0 011 1V20a1 1 0 01-1 1A17 17 0 013 4a1 1 0 011-1h3.5a1 1 0 011 1c0 1.25.2 2.45.57 3.57a1 1 0 01-.25 1z"/></svg></span>
    <p>contact@gnomonvale.com<br><strong>1-800-555-0147</strong></p>
  </div>
  <div class="lang-select"><span class="flag"></span>EN</div>
</header>
<nav class="main-nav">
  <a href="#">Home</a><a href="#">About us</a><a href="#">Show product</a><a href="#">Buy sundial</a><a href="#" class="active">Create sundial</a><a href="#">Event</a><a href="#">Contact us</a>
</nav>
<section class="hero" role="img" aria-label="Photo of a vertical sundial mounted on a wall">
  <h1>CREATE YOUR VERTICAL SUNDIAL</h1>
</section>
<section class="location">
  <div class="map" role="img" aria-label="Satellite map for choosing the sundial location"></div>
  <div class="location-copy">
    <h2 class="section-title">SUNDIAL LOCATION</h2>
    <p>Select the location where you want to place your paper sundial. Zoom in to the exact building and drag the marker to its wall, or type the coordinates below to set the position.</p>
    <div class="coords"><span>Longitude</span><span class="field"></span><span>Latitude</span><span class="field"></span><span>Wall declination</span><span class="field"></span></div>
    <button class="btn-go">Go</button>
    <h3>Now select the face of the building</h3>
    <p>Pick the wall that will hold your sundial. The face direction sets the declination, so the hour lines match the sun on that side of the building.</p>
  </div>
</section>
<section class="options">
  <h2 class="section-title">SUNDIAL OPTIONS</h2>
  <div class="photo wall" role="img" aria-label="Paper sundial fixed on a brick wall"></div>
  <div class="photo window" role="img" aria-label="Paper sundial placed on a window"></div>
  <div class="choice" style="left:210px"><span class="radio on"></span>Wall sundial</div>
  <div class="choice" style="left:500px"><span class="radio"></span>Window sundial</div>
  <div class="form-row" style="top:322px">
    <span>Banner</span><span class="field" style="width:140px"></span>
    <span class="opt"><span class="radio"></span>Solar Time</span>
    <span class="opt"><span class="radio on"></span>Civil Time</span>
  </div>
  <div class="form-row" style="top:360px">
    <span>Timezone</span><span class="field" style="width:130px">GMT-11 Midway Islands Samoa</span>
    <span class="opt"><span class="radio"></span>Daylight Saving Time</span>
    <span class="opt"><span class="radio"></span>Equation of time</span>
    <button class="btn-create">Create sundial</button>
  </div>
</section>
<footer class="site-footer">
  <div class="footer-col newsletter">
    <h4>Sign up for newsletter</h4>
    <p>Get news, sundial tips and special offers delivered to your inbox.</p>
    <div class="field">Enter Name</div>
    <div class="inline"><div class="field">Enter Email</div><button class="btn-subscribe">SUBSCRIBE</button></div>
  </div>
  <div class="footer-col contact">
    <h4>Contact us</h4>
    <ul>
      <li><span class="dot"></span>Monday to Friday: 9am to 6pm</li>
      <li><span class="dot"></span>Sunday: 10am to 2pm</li>
      <li><span class="dot"></span>Toll free: 1-800-555-0147</li>
      <li><span class="dot"></span>contact@gnomonvale.com</li>
    </ul>
    <div class="social"><span></span><span></span><span></span></div>
  </div>
  <div class="footer-col links">
    <h4 style="text-transform:none">Quick Links</h4>
    <ul>
      <li>Create a paper sundial</li><li>Sundial buying guide</li><li>How sundials work</li><li>Sundial history</li><li>Installation advice</li><li>Sundial gallery and events</li><li>Shipping and returns</li>
    </ul>
  </div>
  <span class="footer-mark"></span>
</footer>
<div class="copyright">©2015 - 2016 GnomonVale. All Rights Reserved</div>
</body>
</html>
```